App Design - Career Prep Pal

We require an App Design for our new App called 'Hiring Helper'. This app is essentially an assistant to help Users prepare for job interviews, to help them get hired. <br/><br/>Users who download the App can view common Questions and Answers, save their favourite responses and also view common Interview Tips. <br/><br/>The vision for our App is for Users who are preparing for an interview (1 week before, 1 day before, even 1 hour before), are able to download, view and educate themselves on common questions and responses, and then be confident to land the job. <br/><br/>Our team has developed wireframes to help highlight what each screen should do and include. Please see attached document, which also highlights key requirements for the experience. Feel free to add/remove/edit what you see on these wireframes. Our preference is that you use Adobe XD please.<br/><br/>In terms of design guidelines, we want the experience to be simple, intuitive and 'memorable' to help Users to remember the questions/responses when they are in the interview. <br/><br/>The final design should communicate 'neat and clean professionalism'; we like the design of: jobvista net au<br/><br/>Thank you for reading! Good luck !

Target Market(s)

Professional job seekers

Font styles to use
Sans Serif

Colors

Designer to choose colors to be used in the design.

Requirements
Must have
• Please see my PixelGuild_UX file that I have uploaded
Nice to have
• Could you also please include some ideas on how we can incorporate Advertising into the app screens

```html
<!DOCTYPE html>
<html lang="en">
<head>
<meta charset="utf-8">
<title>Hiring Helper – View Question &amp; Responses</title>
<link rel="stylesheet" href="https://fonts.googleapis.com/css2?family=Montserrat:wght@800&family=Nunito:wght@400;600&display=swap">
<style>
  :root {
    --brand-blue: #1655e3;
    --brand-blue-deep: #0f49cf;
    --badge-blue: #1a4fc8;
    --page-bg: #f4f4f4;
    --card-bg: #ffffff;
    --ink: #111111;
    --body-ink: #1e1e1e;
    --white: #ffffff;
  }
  * { box-sizing: border-box; margin: 0; padding: 0; }
  html, body { width: 1200px; height: 2598px; overflow: hidden; }
  body {
    background: var(--page-bg);
    font-family: "Nunito", sans-serif;
    color: var(--body-ink);
    position: relative;
  }
  .app-header {
    position: absolute; left: 0; top: 0;
    width: 1200px; height: 425px;
    background: linear-gradient(160deg, #1b5fe8 0%, var(--brand-blue) 45%, var(--brand-blue-deep) 100%);
    color: var(--white);
  }
  .header-photo {
    position: absolute; inset: 0;
    background: radial-gradient(ellipse at 30% 70%, rgba(10,40,150,0.35), transparent 55%),
                radial-gradient(ellipse at 75% 40%, rgba(255,255,255,0.08), transparent 60%);
  }
  .status-bar {
    position: absolute; left: 0; top: 0; width: 100%; height: 110px;
  }
  .status-time {
    position: absolute; left: 40px; top: 34px;
    font-family: "Nunito", sans-serif; font-weight: 600;
    font-size: 40px; letter-spacing: 0.5px;
  }
  .status-icons { position: absolute; right: 40px; top: 42px; }
  .nav-bar {
    position: absolute; left: 0; top: 195px; width: 100%; height: 90px;
    display: flex; align-items: center;
  }
  .back-button { position: absolute; left: 40px; top: 24px; }
  .screen-title {
    position: absolute; left: 140px; top: 12px;
    font-family: "Montserrat", sans-serif; font-weight: 800;
    font-size: 59px; letter-spacing: -0.5px; line-height: 66px;
    white-space: nowrap;
  }
  .category-title {
    position: absolute; left: 0; top: 505px; width: 1200px;
    text-align: center;
    font-family: "Montserrat", sans-serif; font-weight: 800;
    font-size: 50px; letter-spacing: -1.5px; line-height: 66px;
    color: var(--ink);
  }
  .question-list { list-style: none; }
  .question-card {
    position: absolute; left: 48px; width: 1109px; height: 333px;
    background: var(--card-bg);
    border-radius: 20px;
    box-shadow: 0 4px 18px rgba(0,0,0,0.06);
    display: flex; align-items: center;
  }
  .question-number {
    position: absolute; left: 43px; top: 96px;
    width: 141px; height: 141px; border-radius: 50%;
    background: var(--badge-blue);
    color: var(--white);
    box-shadow: 0 12px 16px rgba(0,0,0,0.18);
    display: flex; align-items: center; justify-content: center;
    font-family: "Nunito", sans-serif; font-weight: 400;
    font-size: 104px; line-height: 1;
  }
  .question-text {
    position: absolute; left: 220px; top: 82px; width: 860px;
    font-size: 23.8px; line-height: 41.6px;
  }
</style>
</head>
<body>
  <header class="app-header">
    <div class="header-photo" role="img" aria-label="Blue-tinted photo of a person writing notes with a pen at a desk"></div>
    <div class="status-bar">
      <span class="status-time">9:41</span>
      <svg class="status-icons" width="165" height="30" viewBox="0 0 165 30" aria-hidden="true">
        <g fill="#fff">
          <rect x="0" y="20" width="7" height="9" rx="1"/>
          <rect x="11" y="15" width="7" height="14" rx="1"/>
          <rect x="22" y="9" width="7" height="20" rx="1"/>
          <rect x="33" y="2" width="7" height="27" rx="1"/>
          <path d="M70 28 l-6 -7 a9 9 0 0 1 12 0 z"/>
          <path d="M57 13 a19 19 0 0 1 26 0 l-3.5 4 a14 14 0 0 0 -19 0 z"/>
          <path d="M51 7 a27 27 0 0 1 38 0 l-3.5 4 a22 22 0 0 0 -31 0 z"/>
          <rect x="109" y="2" width="50" height="26" rx="7" fill="none" stroke="#fff" stroke-width="2.5" opacity="0.6"/>
          <rect x="113" y="6" width="42" height="18" rx="4"/>
          <rect x="161" y="10" width="3" height="10" rx="1.5" opacity="0.6"/>
        </g>
      </svg>
    </div>
    <nav class="nav-bar">
      <svg class="back-button" width="44" height="40" viewBox="0 0 44 40" aria-label="Back">
        <path d="M42 20 H5 M20 4 L4 20 L20 36" fill="none" stroke="#fff" stroke-width="5" stroke-linecap="round" stroke-linejoin="round"/>
      </svg>
      <h1 class="screen-title">VIEW QUESTION &amp; RESPONSES</h1>
    </nav>
  </header>

  <h2 class="category-title">BEHAVIOURAL</h2>

  <ol class="question-list">
    <li class="question-card" style="top:659px">
      <span class="question-number">1</span>
      <p class="question-text">Lorem Ipsum is simply dummy text of the printing and typesetting industry. Lorem Ipsum has been the industry's standard dummy text ever since the 1500s, when an unknown printer took a galley of type and scrambled it to make a type specimen book. It has survived not only five centuries,</p>
    </li>
    <li class="question-card" style="top:1053px">
      <span class="question-number">2</span>
      <p class="question-text">Lorem Ipsum is simply dummy text of the printing and typesetting industry. Lorem Ipsum has been the industry's standard dummy text ever since the 1500s, when an unknown printer took a galley of type and scrambled it to make a type specimen book. It has survived not only five centuries,</p>
    </li>
    <li class="question-card" style="top:1446px">
      <span class="question-number">3</span>
      <p class="question-text">Lorem Ipsum is simply dummy text of the printing and typesetting industry. Lorem Ipsum has been the industry's standard dummy text ever since the 1500s, when an unknown printer took a galley of type and scrambled it to make a type specimen book. It has survived not only five centuries,</p>
    </li>
    <li class="question-card" style="top:1830px">
      <span class="question-number">4</span>
      <p class="question-text">Lorem Ipsum is simply dummy text of the printing and typesetting industry. Lorem Ipsum has been the industry's standard dummy text ever since the 1500s, when an unknown printer took a galley of type and scrambled it to make a type specimen book. It has survived not only five centuries,</p>
    </li>
    <li class="question-card" style="top:2221px">
      <span class="question-number">5</span>
      <p class="question-text">Lorem Ipsum is simply dummy text of the printing and typesetting industry. Lorem Ipsum has been the industry's standard dummy text ever since the 1500s, when an unknown printer took a galley of type and scrambled it to make a type specimen book. It has survived not only five centuries,</p>
    </li>
  </ol>
</body>
</html>
```